Freelance business trainer needs a new business card

My business is called Brontlearn. I provide training in the workplace on management, coaching and mentoring, and customer service topics for a variety of businesses, colleges and private training providers, and teach on management programs. I need a professional but eye catching business card. Business colours grey and orange. My name Marion Tadwick; Tel 07382 415067; email mtadwick@brontlearn.co.uk; website www.brontlearn.co.uk.
Happy to have some sort of logo on front and details on back or all on one side
Target Market(s)
SME businesses and colleges - workshops i run are for adults in the workplace
Industry/Entity Type
Training
Look and feel

```html
<!DOCTYPE html>
<html lang="en">
<head>
<meta charset="utf-8">
<title>Brontlearn Business Card</title>
<link rel="stylesheet" href="https://fonts.googleapis.com/css2?family=Mulish:wght@400;600;800&display=swap">
<style>
  :root {
    --orange: #f7901e;
    --grey: #4a4849;
    --grey-text: #4d4d4d;
    --white: #ffffff;
    --backdrop: #e9e7e4;
  }
  * { margin: 0; padding: 0; box-sizing: border-box; }
  html, body { width: 1200px; height: 631px; overflow: hidden; }
  body {
    background: var(--backdrop);
    font-family: "Mulish", sans-serif;
    display: flex;
    align-items: center;
    justify-content: center;
    gap: 40px;
  }
  .card {
    position: relative;
    width: 540px;
    height: 310px;
    background: var(--white);
    overflow: hidden;
    box-shadow: 0 6px 18px rgba(0,0,0,0.18);
  }
  .card-strip {
    position: absolute;
    left: 0; right: 0; bottom: 0;
    height: 14px;
    background: var(--orange);
  }

  /* Front */
  .front-brand {
    position: absolute;
    left: 0; right: 0; top: 108px;
    text-align: center;
  }
  .brand-name {
    font-weight: 800;
    font-size: 58px;
    line-height: 1;
    color: var(--orange);
    letter-spacing: -1px;
  }
  .brand-tagline {
    display: inline-block;
    margin-top: 6px;
    background: var(--grey);
    color: var(--white);
    font-weight: 600;
    font-size: 15px;
    padding: 3px 10px;
    white-space: nowrap;
  }

  /* Back */
  .back-shapes { position: absolute; inset: 0; }
  .back-intro {
    position: absolute;
    left: 24px; top: 20px;
    width: 282px;
    font-size: 10px;
    line-height: 2.05;
    font-weight: 600;
    color: var(--orange);
  }
  .back-intro strong { color: var(--grey); font-weight: 800; }
  .back-brand {
    position: absolute;
    left: 350px; top: 78px;
    width: 182px;
    text-align: center;
  }
  .back-brand .brand-name { font-size: 31px; letter-spacing: -0.5px; }
  .back-brand .brand-tagline {
    background: none;
    padding: 0;
    margin-top: 4px;
    font-size: 8.5px;
  }
  .holder {
    position: absolute;
    left: 22px; top: 170px;
    color: var(--white);
  }
  .holder-name { font-weight: 800; font-size: 19px; }
  .holder-role, .holder-credentials { font-size: 11.5px; line-height: 1.45; }
  .contact-list {
    position: absolute;
    right: 18px; top: 204px;
    list-style: none;
  }
  .contact-item {
    display: flex;
    align-items: center;
    justify-content: flex-end;
    gap: 10px;
    height: 24px;
    margin-bottom: 3px;
    font-size: 12px;
    color: var(--grey-text);
  }
  .contact-icon {
    width: 21px; height: 21px;
    background: var(--grey);
    display: flex; align-items: center; justify-content: center;
  }
</style>
</head>
<body>

  <section class="card card-front">
    <div class="front-brand">
      <div class="brand-name">Brontlearn</div>
      <div class="brand-tagline">Professional Workplace Training Services</div>
    </div>
    <div class="card-strip"></div>
  </section>

  <section class="card card-back">
    <svg class="back-shapes" width="540" height="310" viewBox="0 0 540 310" aria-hidden="true">
      <circle cx="470" cy="58" r="150" fill="var(--grey)"/>
      <circle cx="110" cy="330" r="185" fill="var(--orange)"/>
    </svg>

    <p class="back-intro"><strong>Brontlearn</strong> provides a range of workplace management &amp; business training, empowering &amp; encouraging employees to fully utilise skills &amp; knowledge learnt to enhance their working practices &amp; achieve objectives.</p>

    <div class="back-brand">
      <div class="brand-name">Brontlearn</div>
      <div class="brand-tagline">Professional Workplace Training Services</div>
    </div>

    <div class="holder">
      <div class="holder-name">Marion Tadwick</div>
      <div class="holder-role">Owner/Lead Trainer</div>
      <div class="holder-credentials">MCMI, MIFL, CertEd, PGCCM, TIOSH</div>
    </div>

    <ul class="contact-list">
      <li class="contact-item">07382 415067
        <span class="contact-icon"><svg width="11" height="15" viewBox="0 0 11 15"><rect x="1" y="1" width="9" height="13" rx="1.5" fill="none" stroke="#fff" stroke-width="1.3"/><circle cx="5.5" cy="11.5" r="0.9" fill="#fff"/></svg></span>
      </li>
      <li class="contact-item">mtadwick@brontlearn.co.uk
        <span class="contact-icon"><svg width="14" height="10" viewBox="0 0 14 10"><rect x="0.7" y="0.7" width="12.6" height="8.6" fill="none" stroke="#fff" stroke-width="1.3"/><path d="M1 1 L7 6 L13 1" fill="none" stroke="#fff" stroke-width="1.3"/></svg></span>
      </li>
      <li class="contact-item">www.brontlearn.co.uk
        <span class="contact-icon"><svg width="14" height="14" viewBox="0 0 14 14"><circle cx="7" cy="7" r="6" fill="none" stroke="#fff" stroke-width="1.3"/><ellipse cx="7" cy="7" rx="2.6" ry="6" fill="none" stroke="#fff" stroke-width="1.1"/><path d="M1 7 H13" stroke="#fff" stroke-width="1.1"/></svg></span>
      </li>
    </ul>

    <div class="card-strip"></div>
  </section>

</body>
</html>
```